Laser Tattoo Removal Business Cards

We are looking for a professional business card design for a laser tattoo removal business. Ideally looking for a black business card design. The name of the business is Brightline Tattoo Removal. We place our cards at local tattoo shops so we ideally are looking for something trendy/edgy to draw both male and female clientele in.

Target Market(s)

Male/Female ages 18-60

Contact Information for Business Card

black background ideally.. hoping to stay within greys, whites and black

Font styles to use
Serif
Sans Serif

Colors
121212
a9a9a9
5c5c5c
f5f5f5
ffffff
7f7f7f
606060
848484
9d9d9d

Requirements
Must have
• Employee Info:
• Melissa Thornbury
• Chief Executive Offer
• m: 919.537.2846
• w: 919.362.4178
• f: 919.685.3907
• mthornbury@brightlinetattooremoval.example
• Address:
• 4615 Oakmere Pkwy, Suite 210
• Raleigh, NC 27654
• Website:
• www.brightlinetattooremoval.example
Nice to have
• Myabe business name on back or logo on back and employee info on the front

```html
<!DOCTYPE html>
<html lang="en">
<head>
<meta charset="utf-8">
<title>Brightline Tattoo Removal – Business Card</title>
<link rel="stylesheet" href="https://fonts.googleapis.com/css2?family=Antonio:wght@300;400&family=Roboto+Condensed:wght@400;500&family=Roboto:wght@400&family=Montserrat:wght@400;700&display=swap">
<style>
  :root {
    --stage-light: #d4d4d4;
    --stage-dark: #868686;
    --card-white: #ffffff;
    --pattern-soft: #f5f5f5;
    --ink: #121212;
    --ink-mid: #5c5c5c;
    --ink-soft: #7f7f7f;
    --rule: #606060;
    --band: #262626;
    --back-black: #1b1b1d;
    --frame-line: #9d9d9d;
    --mark-white: #f5f5f5;
  }
  * { margin: 0; padding: 0; box-sizing: border-box; }
  html, body { width: 1200px; height: 960px; overflow: hidden; }
  body {
    position: relative;
    background: linear-gradient(90deg, var(--stage-light) 0%, #b0b0b0 50%, var(--stage-dark) 100%);
  }

  /* Front side */
  .card-front {
    position: absolute;
    left: 302px; top: 122px;
    width: 600px; height: 343px;
    background: var(--card-white);
    overflow: hidden;
  }
  .card-front__texture {
    position: absolute; inset: 0 0 11px 0;
    background: radial-gradient(ellipse at 60% 45%, #fafafa 0%, var(--pattern-soft) 70%, #efefef 100%);
  }
  .card-front__band {
    position: absolute; left: 0; right: 0; bottom: 0; height: 11px;
    background: var(--band);
  }
  .employee-name {
    position: absolute; left: 46px; top: 120px;
    font-family: "Antonio", "Oswald", sans-serif;
    font-weight: 400; font-size: 37px; line-height: 1;
    letter-spacing: 0.5px;
    color: var(--ink);
  }
  .employee-title {
    position: absolute; left: 45px; top: 161px;
    font-family: "Roboto Condensed", sans-serif;
    font-weight: 500; font-size: 13.5px; line-height: 1;
    color: var(--ink-soft);
    letter-spacing: 0.3px;
  }
  .employee-email {
    position: absolute; left: 46px; top: 179px;
    font-family: "Roboto Condensed", sans-serif;
    font-size: 13.5px; line-height: 1;
    color: var(--ink-soft);
  }
  .contact-block {
    position: absolute; left: 46px; top: 211px;
    display: flex; align-items: stretch;
    font-family: "Roboto", sans-serif;
    font-size: 13.5px; line-height: 18px;
    color: var(--ink-mid);
  }
  .contact-phones { list-style: none; }
  .contact-divider {
    width: 1px; background: var(--rule);
    margin: 2px 16px 0 14px;
  }
  .contact-address { font-style: normal; }
  .website {
    position: absolute; left: 45px; top: 282px;
    font-family: "Montserrat", sans-serif;
    font-size: 13.5px; line-height: 1;
    letter-spacing: 1.4px;
    color: var(--ink-mid);
  }
  .website__name { font-weight: 700; }
  .website__tld { font-weight: 400; letter-spacing: 0.6px; color: var(--ink-soft); }

  /* Back side */
  .card-back {
    position: absolute;
    left: 299px; top: 495px;
    width: 600px; height: 343px;
    background: var(--back-black);
  }
  .card-back__frame {
    position: absolute; left: 9px; top: 9px; right: 9px; bottom: 11px;
    border: 1px solid var(--frame-line);
    display: flex; align-items: center; justify-content: center;
  }
  .brand-name {
    font-family: "Antonio", "Oswald", sans-serif;
    font-weight: 400; font-size: 30px;
    letter-spacing: 5px;
    text-transform: uppercase;
    color: var(--mark-white);
  }
</style>
</head>
<body>

  <section class="card-front" aria-label="Business card front">
    <div class="card-front__texture" role="img" aria-label="Soft light grey damask pattern background"></div>
    <h1 class="employee-name">MELISSA THORNBURY</h1>
    <p class="employee-title">CHIEF EXECUTIVE OFFER</p>
    <p class="employee-email">mthornbury@brightlinetattooremoval.example</p>
    <div class="contact-block">
      <ul class="contact-phones">
        <li>919.537.2846 (m)</li>
        <li>919.362.4178 (w)</li>
        <li>919.685.3907 (f)</li>
      </ul>
      <span class="contact-divider"></span>
      <address class="contact-address">
        4615 Oakmere Pkwy<br>
        Suite 210<br>
        Raleigh, NC 27654
      </address>
    </div>
    <p class="website"><span class="website__name">BRIGHTLINETATTOOREMOVAL</span><span class="website__tld">.example</span></p>
    <div class="card-front__band"></div>
  </section>

  <section class="card-back" aria-label="Business card back">
    <div class="card-back__frame">
      <p class="brand-name">Brightline Tattoo Removal</p>
    </div>
  </section>

</body>
</html>
```